New manufacturing IT architecture concept powerpoint presentation

Create an appealing PowerPoint presentation, from handmade sketches, to illustrate a new approach to manufacturing IT architectures. We want to present the idea to augment the experience of people working in manufacturing plants using AI based on the data that our systems normally collect. We even want to present the power of having a tier 2 Manufacturing execution system that can coordinate and optimize production between multiple plants of the same corporate. The target audience is IT managers, Operations Managers, plant managers, engineering managers, and Continuous improvement managers.
Target Market(s)
Manufacturing companies mostly in Food & Bev and CPG. Mostly big multinational companies
Industry/Entity Type
Software manufacturing solutions (MES/MOM)
Font styles to use
Other font styles liked:
- Segoe
Look and feel

```html
<!DOCTYPE html>
<html lang="en">
<head>
<meta charset="utf-8">
<title>NOVA OPS – Presentation Overview</title>
<link rel="stylesheet" href="https://fonts.googleapis.com/css2?family=Roboto:wght@400;500;700;900&display=swap">
<style>
:root{
  --page:#e8eaed;
  --ink:#1f2328;
  --muted:#555b63;
  --teal:#2aa6a6;
  --blue:#2c7fd1;
  --deep:#1565b8;
  --navy:#16213a;
  --red:#d5121e;
  --line-blue:#123f87;
  --slide-gray:#eceef0;
}
*{margin:0;padding:0;box-sizing:border-box}
html,body{width:828px;height:1200px;overflow:hidden}
body{background:var(--page);font-family:"Roboto",Arial,sans-serif;color:var(--ink);position:relative}
.slide{position:absolute;width:366px;height:206px;background:#fff;overflow:hidden;box-shadow:0 2px 8px rgba(0,0,0,.12)}
.col-l{left:34px}.col-r{left:428px}
.row-1{top:38px}.row-2{top:265px}.row-3{top:496px}.row-4{top:726px}.row-5{top:957px}
.slide-title{position:absolute;left:21px;top:11px;font-size:7.3px;font-weight:500;letter-spacing:.1px;z-index:2}
.rule{position:absolute;left:0;top:26px;width:248px;height:2px;background:var(--teal);z-index:2}
.brand{position:absolute;right:21px;top:6px;font-size:16px;font-weight:700;color:var(--blue);letter-spacing:.3px;z-index:2}
.photo{position:absolute}
.ic{position:absolute;width:24px;height:24px;border-radius:50%;background:#fff;box-shadow:0 1px 4px rgba(0,0,0,.16);display:flex;align-items:center;justify-content:center}
.ic svg{width:12px;height:12px;fill:none;stroke:var(--blue);stroke-width:1.4;stroke-linecap:round;stroke-linejoin:round}
.feat-h{position:absolute;font-size:5.4px;font-weight:700;text-transform:uppercase}
.feat-p{position:absolute;font-size:4.5px;line-height:1.45;color:var(--muted)}

/* cover */
.cover .photo{inset:0;background:linear-gradient(120deg,#0f2a4a 0%,#1d4f7a 45%,#3b6b8f 62%,#0e1c30 100%)}
.cover-title{position:absolute;left:21px;top:80px;font-size:10.4px;line-height:15.6px;font-weight:700;color:#fff;text-transform:uppercase}
.cover .brand{color:#fff}

/* intro */
.intro .photo{inset:0;background:linear-gradient(180deg,#e3f4fb 0%,#d4ecf5 55%,#eaf2f7 100%)}
.pillar{position:absolute;width:64px;height:64px;border-radius:50%;background:#fff;box-shadow:0 2px 8px rgba(0,0,0,.14);display:flex;flex-direction:column;align-items:center;justify-content:center;text-align:center;font-size:4.2px;line-height:1.6;text-transform:uppercase;padding:0 7px}
.pillar svg{width:16px;height:16px;margin-bottom:5px;fill:none;stroke:var(--blue);stroke-width:1.3}
.pillar.main{background:var(--deep);color:#fff}
.pillar.main svg{stroke:#fff}

/* technology */
.tech h2{position:absolute;left:218px;top:83px;font-size:9.3px;font-weight:500}
.tech p{position:absolute;left:218px;top:101px;width:130px;font-size:6.1px;line-height:1.7;color:var(--muted)}

/* kpi bullets */
.kpi-list{position:absolute;font-size:6px;font-weight:500}
.kpi-list li{list-style:none;display:flex;align-items:center;gap:5px;height:11.5px}
.kpi-list li::before{content:"";width:4px;height:4px;border-radius:50%;border:1.2px solid var(--blue)}

/* sme */
.sme-lead{position:absolute;left:21px;top:41px;font-size:6.8px;font-weight:500}
.sme-item{position:absolute;left:53px;font-size:5.7px;line-height:1.6;color:var(--muted)}

/* activity */
.activity{background:var(--slide-gray)}
.node-label{position:absolute;font-size:4.6px;font-weight:700}

/* chart */
.chart .photo{inset:0;background:linear-gradient(90deg,#ffffff 0%,#f4f9fc 50%,#deedf6 100%)}
.axis-label{font-size:3.6px;fill:#333;font-family:"Roboto",Arial,sans-serif}
.legend{position:absolute;top:189px;display:flex;align-items:center;gap:5px;font-size:6.2px}
.legend i{display:block;width:22px;height:8px}

/* closing */
.closing .photo{inset:0;background:linear-gradient(135deg,#12223a 0%,#1b3250 60%,#0f1a2c 100%)}
.closing .teal-panel{position:absolute;inset:0}
.closing .brand{color:#fff}
.thanks{position:absolute;left:0;right:0;top:78px;text-align:center;font-size:27px;font-weight:900;color:#fff;letter-spacing:.5px}
.contact{position:absolute;top:170px;display:flex;align-items:center;gap:9px;font-size:5.5px;line-height:1.5;color:#fff;font-weight:500}
.contact .ic{position:static;width:22px;height:22px}
.contact .ic svg{width:10px;height:10px}
</style>
</head>
<body>

<!-- Cover -->
<section class="slide col-l row-1 cover">
  <div class="photo" role="img" aria-label="Hands holding a tablet surrounded by glowing hexagon technology icons"></div>
  <svg width="366" height="206" style="position:absolute;inset:0">
    <polygon points="0,0 31,0 0,31" fill="#fff"/>
    <polygon points="31,0 38,0 0,38 0,31" fill="var(--teal)"/>
    <rect x="0" y="38" width="6" height="168" fill="var(--teal)"/>
  </svg>
  <div class="brand">NOVA OPS</div>
  <h1 class="cover-title">Connected Operation Hub &amp;<br>Augmented Plant<br>Management</h1>
</section>

<!-- Introduction -->
<section class="slide col-r row-1 intro">
  <div class="photo" role="img" aria-label="Pale blue city skyline with digital data streams"></div>
  <div class="slide-title">INTRODUCTION TO NOVA OPS</div>
  <div class="rule"></div>
  <div class="brand">NOVA OPS</div>
  <svg width="366" height="206" style="position:absolute;inset:0">
    <path d="M104,144 Q130,158 148,136" fill="none" stroke="#8b959e" stroke-width="2"/>
    <polygon points="150,131 152,142 143,139" fill="#8b959e"/>
    <path d="M260,80 Q238,66 216,82" fill="none" stroke="#8b959e" stroke-width="2"/>
    <polygon points="213,86 214,76 222,81" fill="#8b959e"/>
  </svg>
  <div class="pillar" style="left:46px;top:78px">
    <svg viewBox="0 0 16 16"><circle cx="8" cy="8" r="6.5"/><circle cx="8" cy="6" r="1.6"/><circle cx="5" cy="9.5" r="1.3"/><circle cx="11" cy="9.5" r="1.3"/></svg>Augment people</div>
  <div class="pillar main" style="left:151px;top:78px">
    <svg viewBox="0 0 16 16"><rect x="3" y="2.5" width="9" height="11" rx="1"/><path d="M5 6h5M5 8.5h5M5 11h3"/></svg>Augmented plant management</div>
  <div class="pillar" style="left:257px;top:78px">
    <svg viewBox="0 0 16 16"><circle cx="8" cy="8" r="3"/><path d="M8 1.5v2M8 12.5v2M1.5 8h2M12.5 8h2M3.4 3.4l1.4 1.4M11.2 11.2l1.4 1.4M3.4 12.6l1.4-1.4M11.2 4.8l1.4-1.4"/></svg>Augment corporate visibility</div>
</section>

<!-- Technology -->
<section class="slide col-l row-2 tech">
  <svg width="366" height="206" style="position:absolute;inset:0">
    <polygon points="0,0 236,0 171,206 0,206" fill="url(#techFill)" role="img" aria-label="Two engineers wearing VR headsets over a holographic city model"/>
    <polygon points="236,0 244,0 179,206 171,206" fill="var(--deep)"/>
    <polygon points="224,41 230,41 183,206 177,206" fill="var(--teal)"/>
    <defs><linearGradient id="techFill" x1="0" y1="0" x2="1" y2="1"><stop offset="0" stop-color="#b9c9d6"/><stop offset=".5" stop-color="#4f7497"/><stop offset="1" stop-color="#1b2f48"/></linearGradient></defs>
  </svg>
  <div class="brand">NOVA OPS</div>
  <h2>OUR TECHNOLOGY</h2>
  <p>How digitalization evolved in last years from being technology focused to user and value focused</p>
</section>

<!-- Linked KPIs 1 -->
<section class="slide col-r row-2">
  <div class="slide-title">LINKED KPIS</div>
  <div class="rule"></div>
  <div class="brand">NOVA OPS</div>
  <div class="photo" style="left:21px;top:48px;width:144px;height:134px;background:linear-gradient(135deg,#2c4f78,#0d1a2e)" role="img" aria-label="Hand on a keyboard below a holographic city of connected buildings"></div>
  <ul class="kpi-list" style="left:185px;top:62px"><li>Global</li><li>Regional</li></ul>
  <ul class="kpi-list" style="left:239px;top:62px"><li>Plant/facility/operations</li><li>Equipment</li></ul>
  <div class="ic" style="left:182px;top:100px"><svg viewBox="0 0 12 12"><circle cx="6" cy="6" r="2"/><circle cx="6" cy="6" r="4.5"/></svg></div>
  <div class="feat-h" style="left:215px;top:100px">Operations manager:</div>
  <div class="feat-p" style="left:215px;top:108px;width:130px">Can take decisions with a corporate vision and dispatch them to plants. Any decision become instantly action</div>
  <div class="ic" style="left:182px;top:135px"><svg viewBox="0 0 12 12"><circle cx="6" cy="3.5" r="1.8"/><circle cx="3.5" cy="8" r="1.8"/><circle cx="8.5" cy="8" r="1.8"/></svg></div>
  <div class="feat-h" style="left:215px;top:135px">Cross functional collaboration:</div>
  <div class="feat-p" style="left:215px;top:143px;width:130px">Data and information of different departments are correlated and generate an holistic view to take decision in close loop</div>
</section>

<!-- Subject matter expert -->
<section class="slide col-l row-3">
  <div class="slide-title">SUBJECT MATTTER EXPERT</div>
  <div class="rule"></div>
  <div class="brand">NOVA OPS</div>
  <div class="sme-lead">Main challenged companies face today:</div>
  <div class="ic" style="left:20px;top:58px"><svg viewBox="0 0 12 12"><circle cx="6" cy="6" r="4.5"/><path d="M6 9V5M6 6.5c-1.5 0-2.5-1-2.5-2.5M6 6c1.5 0 2.5-1 2.5-2.5"/></svg></div>
  <div class="sme-item" style="top:66px">Sustainability</div>
  <div class="ic" style="left:20px;top:87px"><svg viewBox="0 0 12 12"><path d="M6 1.5l4 2.3v4.4L6 10.5 2 8.2V3.8z M6 6v4.5M6 6l4-2.2M6 6L2 3.8"/></svg></div>
  <div class="sme-item" style="top:89px">Flexibility ⟶ availability of assets, experience<br>(SMEs), decisions</div>
  <div class="ic" style="left:20px;top:115px"><svg viewBox="0 0 12 12"><circle cx="6" cy="6" r="2"/><circle cx="6" cy="6" r="4.5" stroke-dasharray="2 1.5"/></svg></div>
  <div class="sme-item" style="top:123px">Workforce demographic ⟶ experience, decisions</div>
  <div class="ic" style="left:20px;top:143px"><svg viewBox="0 0 12 12"><rect x="1.5" y="2" width="9" height="8"/><circle cx="6" cy="6" r="1.5"/></svg></div>
  <div class="sme-item" style="top:151px">Corporate wide visibility and coordination</div>
  <div class="ic" style="left:20px;top:172px"><svg viewBox="0 0 12 12"><circle cx="6" cy="6" r="4.5"/><path d="M4 5h4l-1.5-1.5M8 7H4l1.5 1.5"/></svg></div>
  <div class="sme-item" style="top:180px">Supply Chain visibility and coordination</div>
  <div class="photo" style="left:201px;top:47px;width:144px;height:134px;background:radial-gradient(circle at 30% 58%,#8fc7ff 0%,#2d6fd0 30%,#173f80 70%,#0f2650 100%)" role="img" aria-label="Businessman touching a glowing blue gear interface"></div>
</section>

<!-- Linked KPIs 2 -->
<section class="slide col-r row-3">
  <div class="slide-title">LINKED KPIS</div>
  <div class="rule"></div>
  <div class="brand">NOVA OPS</div>
  <div class="ic" style="left:21px;top:57px"><svg viewBox="0 0 12 12"><rect x="2" y="2" width="3" height="3"/><rect x="7" y="7" width="3" height="3"/><path d="M5 3.5h3.5V7M3.5 5v3.5H7"/></svg></div>
  <div class="feat-h" style="left:53px;top:57px">Supply chain coordination:</div>
  <div class="feat-p" style="left:53px;top:65px;width:132px">Data coming from different plants/systems are correlated to optimize supply chain decisions with a multi plant approach. Internal supply chain managed as a whole</div>
  <div class="ic" style="left:21px;top:97px"><svg viewBox="0 0 12 12"><circle cx="6" cy="6" r="2"/><path d="M6 1v2M6 9v2M1 6h2M9 6h2M2.5 2.5l1.4 1.4M8.1 8.1l1.4 1.4M2.5 9.5l1.4-1.4M8.1 3.9l1.4-1.4"/></svg></div>
  <div class="feat-h" style="left:53px;top:97px">Production optimization:</div>
  <div class="feat-p" style="left:53px;top:105px;width:132px">Production optimized at a corporate level and not only at a plant level. Decisions taken at the corporate operations control level</div>
  <div class="ic" style="left:21px;top:136px"><svg viewBox="0 0 12 12"><circle cx="6" cy="6" r="4.5"/><path d="M1.5 6h9M6 1.5c2 2.5 2 6.5 0 9M6 1.5c-2 2.5-2 6.5 0 9"/></svg></div>
  <div class="feat-h" style="left:53px;top:136px">Knowledge capturing &amp; nurturing:</div>
  <div class="feat-p" style="left:53px;top:144px;width:132px">Knowledge of users collected at corporate level and made available to any user with no geography, time or language limitation. Reduced onboarding, increased efficiency, better engagement</div>
  <div class="photo" style="left:201px;top:47px;width:144px;height:134px;background:linear-gradient(160deg,#5c7081 0%,#2c3d4f 45%,#a05a34 72%,#24303d 100%)" role="img" aria-label="Industrial robot arm in a factory with a digital analytics overlay"></div>
</section>

<!-- Our activity -->
<section class="slide col-l row-4 activity">
  <div class="slide-title">OUR ACTIVITY</div>
  <div class="rule"></div>
  <div class="brand">NOVA OPS</div>
  <svg width="366" height="206" style="position:absolute;inset:0" fill="none" stroke="var(--teal)" stroke-width=".7">
    <circle cx="183" cy="101" r="47"/>
    <path d="M113,48 H140 L156,65"/><path d="M113,102 H136"/><path d="M113,155 H140 L156,138"/>
    <path d="M253,48 H226 L210,65"/><path d="M253,102 H230"/><path d="M253,155 H226 L210,138"/>
    <path d="M183,148 V160"/>
    <g fill="#fff"><circle cx="156" cy="65" r="1.8"/><circle cx="136" cy="102" r="1.8"/><circle cx="156" cy="138" r="1.8"/><circle cx="210" cy="65" r="1.8"/><circle cx="230" cy="102" r="1.8"/><circle cx="210" cy="138" r="1.8"/><circle cx="183" cy="148" r="1.8"/></g>
  </svg>
  <div class="photo" style="left:145px;top:63px;width:76px;height:76px;border-radius:50%;background:radial-gradient(circle at 50% 70%,#d9a45a 0%,#4a4a4a 35%,#151515 75%)" role="img" aria-label="Hands holding a glowing digital globe"></div>
  <div class="ic" style="left:89px;top:36px"><svg viewBox="0 0 12 12"><circle cx="6" cy="6" r="2"/><circle cx="6" cy="6" r="4.3" stroke-dasharray="2 1.3"/></svg></div>
  <div class="ic" style="left:89px;top:90px"><svg viewBox="0 0 12 12"><circle cx="6" cy="6" r="1.3"/><path d="M2 2l3 3M10 2L7 5M2 10l3-3M10 10L7 7"/></svg></div>
  <div class="ic" style="left:89px;top:143px"><svg viewBox="0 0 12 12"><circle cx="6" cy="4" r="1.6"/><path d="M3 10c0-2 1.4-3 3-3s3 1 3 3M1.5 6a4.5 4.5 0 0 1 1.5-3.4M10.5 6A4.5 4.5 0 0 0 9 2.6"/></svg></div>
  <div class="ic" style="left:253px;top:36px"><svg viewBox="0 0 12 12"><rect x="3" y="1.5" width="6" height="7" rx="1.2"/><path d="M3 5.5h6M4 10.5l1-2M8 10.5l-1-2"/></svg></div>
  <div class="ic" style="left:253px;top:90px"><svg viewBox="0 0 12 12"><circle cx="6" cy="6" r="4.5"/><path d="M6 5.5V9M6 3.5v.1"/></svg></div>
  <div class="ic" style="left:253px;top:143px"><svg viewBox="0 0 12 12"><rect x="3" y="1.5" width="6" height="9" rx="1"/><circle cx="6" cy="6" r="1.4"/></svg></div>
  <div class="ic" style="left:171px;top:160px"><svg viewBox="0 0 12 12"><rect x="1.5" y="4" width="6" height="6"/><path d="M4.5 4V1.5h6v6H7.5M5 7l3-3"/></svg></div>
  <div class="node-label" style="right:285px;top:46px">SKILL</div>
  <div class="node-label" style="right:285px;top:100px">CONNECT</div>
  <div class="node-label" style="right:285px;top:153px">COORDINATE</div>
  <div class="node-label" style="left:286px;top:46px">TRAIN</div>
  <div class="node-label" style="left:286px;top:100px">INFORM</div>
  <div class="node-label" style="left:286px;top:153px">AUGMENT</div>
  <div class="node-label" style="left:176px;top:191px">UNIFY</div>
</section>

<!-- Production optimization -->
<section class="slide col-r row-4">
  <div class="slide-title">PRODUCTION OPTIMIZATION</div>
  <div class="rule"></div>
  <div class="brand">NOVA OPS</div>
  <div class="photo" style="left:21px;top:47px;width:144px;height:134px;background:linear-gradient(150deg,#c3ccd4 0%,#6f8598 45%,#21344b 100%)" role="img" aria-label="Engineer holding a tablet with production charts beside robot arms"></div>
  <div class="ic" style="left:181px;top:51px"><svg viewBox="0 0 12 12"><path d="M2 2h6v8H2z"/><circle cx="8.5" cy="7.5" r="2"/></svg></div>
  <div class="feat-h" style="left:213px;top:53px">Historical production:</div>
  <div class="feat-p" style="left:213px;top:61px;width:136px">Based on historical production results and conditions best production scheduling/dispatching/setup is proposed</div>
  <div class="ic" style="left:181px;top:85px"><svg viewBox="0 0 12 12"><path d="M2 10l5-5M7 5a2 2 0 1 1 2 2M2 2l8 8"/></svg></div>
  <div class="feat-h" style="left:213px;top:87px">Line setup:</div>
  <div class="feat-p" style="left:213px;top:95px;width:136px">Based on historical data and environmental data best setup is proposed for product/line/format/...</div>
  <div class="ic" style="left:181px;top:118px"><svg viewBox="0 0 12 12"><path d="M1.5 10.5h9M3 10V7M5 10V5.5M7 10V6.5M9 10V3.5M2.5 5l2.5-2 2 1.5 3-2.5"/></svg></div>
  <div class="feat-h" style="left:213px;top:120px">Production performance:</div>
  <div class="feat-p" style="left:213px;top:128px;width:136px">Analysis of production, line &amp; environment status to suggest best actions to keep production performance in target</div>
  <div class="ic" style="left:181px;top:152px"><svg viewBox="0 0 12 12"><circle cx="6" cy="6" r="4.5" stroke-dasharray="2 1.3"/><path d="M6 3.5v5M4.8 5h2.2"/></svg></div>
  <div class="feat-h" style="left:213px;top:154px">Production forecast:</div>
  <div class="feat-p" style="left:213px;top:162px;width:136px">Analysis of production, line and environment status to forecast production volumes or completion</div>
</section>

<!-- Workforce chart -->
<section class="slide col-l row-5 chart">
  <div class="photo" role="img" aria-label="Soft light blue hexagon technology backdrop"></div>
  <div class="slide-title">WORKFORCE TURNOVER ⟶ MISSING EXPERIENCE</div>
  <div class="rule"></div>
  <div class="brand">NOVA OPS</div>
  <svg width="366" height="206" style="position:absolute;inset:0">
    <g stroke="#d7dbe0" stroke-width=".4">
      <line x1="36" y1="62" x2="335" y2="62"/><line x1="36" y1="78.3" x2="335" y2="78.3"/><line x1="36" y1="94.6" x2="335" y2="94.6"/>
      <line x1="36" y1="110.9" x2="335" y2="110.9"/><line x1="36" y1="127.2" x2="335" y2="127.2"/><line x1="36" y1="143.5" x2="335" y2="143.5"/>
    </g>
    <line x1="36" y1="160" x2="335" y2="160" stroke="#666" stroke-width=".5"/>
    <line x1="36" y1="60" x2="36" y2="160" stroke="#666" stroke-width=".5"/>
    <g class="axis-label" text-anchor="end">
      <text x="33" y="161.3">0</text><text x="33" y="145">1</text><text x="33" y="128.7">2</text><text x="33" y="112.4">3</text><text x="33" y="96.1">4</text><text x="33" y="79.8">5</text><text x="33" y="63.5">6</text>
    </g>
    <g class="axis-label" text-anchor="middle">
      <text x="61" y="168">t1</text><text x="89.5" y="168">t2</text><text x="118" y="168">t3</text><text x="146.5" y="168">t4</text><text x="175" y="168">t5</text>
      <text x="203.5" y="168">t6</text><text x="232" y="168">t7</text><text x="260.5" y="168">t8</text><text x="289" y="168">t9</text><text x="317.5" y="168">t10</text>
    </g>
    <polyline fill="none" stroke="var(--line-blue)" stroke-width=".9" points="36,123.3 67,123.3 95.5,119.2 126.6,111.1 152.6,98.1 183.7,91.5 212,89.1 241,80.1 272,76.1 300.5,68.7 331.6,65.5"/>
    <polyline fill="none" stroke="var(--red)" stroke-width=".9" points="36,119.2 67,119.2 95.5,114.4 126.6,110.3 152.6,111.1 183.7,113.5 212,107.8 241,96.4 272,85 300.5,80.1 331.6,70.4"/>
  </svg>
  <div class="legend" style="left:116px"><i style="background:var(--red)"></i>Knowledge</div>
  <div class="legend" style="left:191px"><i style="background:var(--line-blue)"></i>Experience</div>
</section>

<!-- Closing -->
<section class="slide col-r row-5 closing">
  <div class="photo" role="img" aria-label="Factory floor with engineer and hexagon technology icons in dark blue and teal"></div>
  <svg class="teal-panel" width="366" height="206"><polygon points="161,0 366,0 366,206 260,206" fill="#1f8e92" opacity=".92"/></svg>
  <div class="brand">NOVA OPS</div>
  <div class="thanks">THANK YOU</div>
  <div class="contact" style="left:32px">
    <span class="ic"><svg viewBox="0 0 12 12"><path d="M6 11s3.5-3.6 3.5-6.2a3.5 3.5 0 0 0-7 0C2.5 7.4 6 11 6 11z"/><circle cx="6" cy="4.8" r="1.2"/></svg></span>
    <span>128, Harbor Line Road,<br>United States</span>
  </div>
  <div class="contact" style="left:151px">
    <span class="ic"><svg viewBox="0 0 12 12"><path d="M3 1.5l2 2.5-1.2 1.2a6 6 0 0 0 3 3L8 7l2.5 2-1 1.5C5.5 10.5 1.5 6.5 1.5 2.5z"/></svg></span>
    <span>+1 (555) 010 2040</span>
  </div>
  <div class="contact" style="left:254px">
    <span class="ic"><svg viewBox="0 0 12 12"><rect x="1.5" y="3" width="9" height="6.5"/><path d="M1.5 3L6 6.5 10.5 3"/></svg></span>
    <span>hello@novaops.com</span>
  </div>
</section>

</body>
</html>
```